Web Design for Independent Pet Supply shop.

Larch Critter Depot is a locally owned and operated premium natural pet food store and supply company with 2 thriving retail stores in Bend, Oregon, and a home delivery service. The pet food offered is the best on the market and may be described as “holistic”. Also on offer is a vast selection of toys, training tools, treats, and other supplies, as well as dog washing services that range from "do-it yourself" to "spa." Current site: LarchCritterDepot.com. They need a new, updated and responsive site.
Likes:
Tovanels.com: Natural colors, not loud, pages in motion, simple & clean but very informative.
Dorvikmerin.com: Everything in simple big colorful blocks. The specials run across the top and in motion. This site looks very professional but simple. The information is available several different places.
Plenharvest.com: Again big blocks through out. Very Fun and inviting. Tons of information with videos and recipes and testimonials. Pleasant feel and colors as well.
Dislikes:
Furlix.com: Looks cheap, hate the colors, very busy and over whelming. Hate the old style header bar going across with options. Too many printed words instead of fun images.
Colors should be "natural" tones, warm and soothing. Deep dark blue and greys with earthy wood color.
Do Not Use: Blue violet, violet, red violet

```html
<!DOCTYPE html>
<html lang="en">
<head>
<meta charset="utf-8">
<title>Larch Critter Depot</title>
<link href="https://fonts.googleapis.com/css2?family=Open+Sans:wght@400;600;700&family=Arimo:wght@400;700&family=Alfa+Slab+One&family=Anton&display=swap" rel="stylesheet">
<style>
:root{
  --brown:#b8782e;
  --brown-dark:#9c6321;
  --brown-light:#cf9a55;
  --footer:#b97c35;
  --footer-bar:#a56a26;
  --cream:#f7f2ea;
  --grey-band:#efefef;
  --text:#555;
  --heading:#333;
  --white:#fff;
}
*{margin:0;padding:0;box-sizing:border-box}
html,body{width:735px;height:1200px;overflow:hidden;background:var(--white)}
body{position:relative;font-family:"Open Sans",sans-serif;color:var(--text);font-size:7px}
.abs{position:absolute}
.top-line{left:0;top:0;width:735px;height:2px;background:var(--brown-light)}
.header{left:0;top:2px;width:735px;height:280px;background:var(--cream)}
.logo{left:58px;top:30px;display:flex;align-items:center;gap:6px}
.logo-dot{width:22px;height:22px;border-radius:50%;background:var(--brown)}
.logo-name{font-weight:700;font-size:19px;color:var(--brown);letter-spacing:.2px}
.call{left:556px;top:28px;display:flex;gap:8px;align-items:center}
.call-ring{width:29px;height:29px;border:1.5px solid var(--brown);border-radius:50%;display:flex;align-items:center;justify-content:center}
.call small{display:block;font-family:Arimo,sans-serif;font-size:8.5px;color:#555}
.call b{display:block;font-family:Arimo,sans-serif;font-size:11px;color:var(--brown-light);margin-top:3px}
.nav{left:50px;top:80px;width:635px;height:36px;background:linear-gradient(#c4853a,#ae6f27);display:flex;justify-content:space-around;align-items:center;box-shadow:0 2px 3px rgba(0,0,0,.25)}
.nav a{font-family:Arimo,sans-serif;font-size:7.2px;color:var(--white);text-decoration:none;text-transform:uppercase}
.hero-frame{left:59px;top:114px;width:617px;height:298px;background:var(--white);box-shadow:0 6px 8px -4px rgba(0,0,0,.25)}
.hero-photo{left:65px;top:117px;width:605px;height:290px;background:linear-gradient(100deg,#4a3a26 0%,#6b6a3c 45%,#7f8a4a 70%,#5b6b34 100%)}
.caption{left:299px;top:262px;width:172px;color:var(--white)}
.caption h2{font-family:Anton,sans-serif;font-size:25px;font-weight:400;letter-spacing:.8px;border-top:1px solid #fff;display:inline-block;padding-top:2px;line-height:30px}
.caption p{font-size:8px;line-height:14px;margin-top:1px}
.btn-view{display:inline-block;margin-top:6px;background:var(--brown);color:var(--white);font-size:7px;font-weight:600;padding:6px 19px}
.dots{left:345px;top:392px;width:80px;height:18px;background:var(--white);border-radius:40px 40px 0 0;display:flex;gap:6px;justify-content:center;align-items:center}
.dots i{width:6px;height:6px;border-radius:50%;background:#555}
.dots i.on{background:var(--white);border:2px solid var(--brown);width:9px;height:9px}
.quick{left:472px;top:140px;width:169px;height:248px;background:#f4f4f4}
.quick h3{background:var(--brown);color:var(--white);font-family:Arimo,sans-serif;font-weight:400;font-size:12.5px;letter-spacing:.8px;text-align:center;height:32px;line-height:32px}
.field{margin:11px 12px 0;background:var(--white);height:25px;display:flex;align-items:center;padding-left:8px;gap:8px;font-size:7px;color:#777}
.field.msg{height:56px;align-items:flex-start;padding-top:9px}
.field i{width:5px;height:5px;background:#999;border-radius:1px}
.submit{margin:11px 12px 0;background:linear-gradient(#c88a42,#ad6e27);height:27px;line-height:27px;text-align:center;color:var(--white);font-family:Arimo,sans-serif;font-size:9.5px}
.services-title{left:0;top:436px;width:735px;text-align:center}
.services-title span{font-family:"Alfa Slab One",serif;font-size:17.5px;letter-spacing:.3px;color:var(--brown);border-top:1px solid var(--brown-light);border-bottom:1px solid var(--brown-light);padding:3px 1px;line-height:26px}
.service{top:486px;width:190px;text-align:center}
.service .circle{width:74px;height:74px;border-radius:50%;background:var(--brown);margin:0 auto;display:flex;align-items:center;justify-content:center}
.service h4{font-family:Arimo,sans-serif;font-weight:400;font-size:10px;color:#333;margin-top:9px}
.service p{font-size:7px;line-height:12.5px;margin-top:6px}
.service em{display:block;font-size:7px;color:var(--brown);margin-top:6px}
.band{left:0;top:665px;width:735px;height:342px;background:var(--grey-band)}
.news{left:61px;top:700px;width:405px}
.news h3{font-family:Arimo,sans-serif;font-weight:400;font-size:12.5px;color:var(--heading);line-height:23.5px}
.news p{font-size:7px;line-height:14.3px;margin-top:11px}
.nail-photo{left:60px;top:900px;width:306px;height:79px;background:var(--white);padding:3px;box-shadow:0 1px 3px rgba(0,0,0,.3)}
.nail-photo div{width:100%;height:100%;background:linear-gradient(90deg,#3b3b3b,#8a7b66 30%,#3c3c3c 50%,#8b7a63 78%,#3a3a3a)}
.social{left:482px;top:700px;width:192px;height:279px;background:var(--white);box-shadow:0 1px 4px rgba(0,0,0,.2);padding:18px 20px}
.social-head{display:flex;align-items:center;gap:6px}
.social-head i{width:30px;height:30px;border-radius:50%;background:#d9b47f}
.social-head b{font-size:13px;color:#3b5a9a}
.social-head small{display:block;font-size:5px;color:#555;font-weight:400;margin-top:4px}
.post{display:flex;gap:8px;margin-top:13px}
.post .thumb{width:37px;height:34px;background:linear-gradient(#8b6a46,#c4a27a)}
.post h5{font-weight:400;font-size:7.5px;color:#333}
.post p{font-size:5.5px;color:#666;margin-top:3px}
.post small{display:block;font-size:5.5px;color:#444;margin-top:4px}
.fans-label{font-size:4.5px;margin-top:12px;color:#444}
.fans{display:grid;grid-template-columns:repeat(8,18px);gap:2px;margin-top:4px}
.fans i{height:18px;background:linear-gradient(#a8927a,#6e5a48)}
.plugin{font-size:4px;margin-top:5px;border-top:1px solid #ddd;padding-top:3px;color:#777}
.footer{left:0;top:1007px;width:735px;height:166px;background:var(--footer);color:var(--white)}
.col{top:1026px;color:var(--white)}
.col h4{font-family:Arimo,sans-serif;font-weight:400;font-size:12.5px;border-bottom:1px solid rgba(255,255,255,.6);padding-bottom:4px;display:inline-block}
.col p,.col li{font-size:7px;line-height:13.5px}
.col ul{list-style:none;margin-top:6px}
.col li{line-height:11.6px}
.col li:before{content:"› ";}
.tweet{display:flex;gap:9px;margin-top:10px}
.tweet i{width:11px;height:8px;background:var(--white);border-radius:50% 50% 40% 40%;margin-top:3px;flex:none}
.tweet h5{font-weight:400;font-size:8.5px}
.tweet p{font-size:5.5px;line-height:10px}
.contact-row{display:flex;gap:10px;align-items:center;margin-top:8px;font-size:7px}
.bottom{left:0;top:1173px;width:735px;height:27px;background:var(--footer-bar);color:var(--white);font-size:7px}
.bottom p{position:absolute;left:61px;top:9px}
.rounds{position:absolute;left:575px;top:5px;display:flex;gap:5px}
.rounds i{width:18px;height:18px;border:1px solid rgba(255,255,255,.8);border-radius:50%}
</style>
</head>
<body>
<div class="abs top-line"></div>
<div class="abs header" role="img" aria-label="Soft cream background with faint paw print pattern"></div>

<div class="abs logo"><span class="logo-dot"></span><span class="logo-name">Larch Critter Depot</span></div>
<div class="abs call">
  <span class="call-ring"><svg width="12" height="12" viewBox="0 0 24 24"><path fill="#b8782e" d="M6.6 10.8a15 15 0 0 0 6.6 6.6l2.2-2.2c.3-.3.7-.4 1-.2 1.1.4 2.3.6 3.6.6.6 0 1 .4 1 1V20c0 .6-.4 1-1 1A17 17 0 0 1 3 4c0-.6.4-1 1-1h3.5c.6 0 1 .4 1 1 0 1.3.2 2.5.6 3.6.1.3 0 .7-.2 1z"/></svg></span>
  <div><small>Call Us Now!</small><b>541-820-4417</b></div>
</div>

<svg class="abs" style="left:15px;top:86px" width="40" height="38"><polygon points="0,0 38,0 38,38 0,38 14,19" fill="#a8692a"/></svg>
<svg class="abs" style="left:680px;top:86px" width="40" height="38"><polygon points="2,0 40,0 26,19 40,38 2,38" fill="#a8692a"/></svg>
<nav class="abs nav">
  <a>Home</a><a>Events</a><a>Blog</a><a>About</a><a>Dog Wash</a><a>Products</a><a>Resources</a><a>Links</a><a>Contact</a>
</nav>

<div class="abs hero-frame"></div>
<div class="abs hero-photo" role="img" aria-label="Photo of a chocolate labrador lying on the grass in a garden next to a food bowl"></div>
<div class="abs caption">
  <h2>HAPPY FALL</h2>
  <p>The Larch Critter Depot Dog Wash attendants always here to help wash your four legged friends, and trim their nails</p>
  <span class="btn-view">View more</span>
</div>
<div class="abs dots"><i class="on"></i><i></i><i></i><i></i></div>

<form class="abs quick">
  <h3>QUICK CONTACT</h3>
  <div class="field"><i></i>Enter your name</div>
  <div class="field"><i></i>Enter your email address</div>
  <div class="field"><i></i>Phone number</div>
  <div class="field msg"><i></i>Enter your message</div>
  <div class="submit">SUBMIT</div>
</form>

<div class="abs services-title"><span>SERVICES WE OFFER</span></div>

<div class="abs service" style="left:34px">
  <div class="circle"><svg width="34" height="30" viewBox="0 0 34 30" fill="none" stroke="#fff" stroke-width="1.6"><rect x="5" y="3" width="12" height="16" rx="2"/><path d="M3 22h28l-3 6H6z"/></svg></div>
  <h4>Pup Brew</h4>
  <p>Now you can pour some cold brew for<br>your pup in a fun and easy way that has a<br>delicious flavor and packed full...</p>
  <em>Read more</em>
</div>
<div class="abs service" style="left:272px">
  <div class="circle"><svg width="36" height="22" viewBox="0 0 36 22" fill="none" stroke="#fff" stroke-width="1.6"><path d="M8 9c0-5 20-5 20 0"/><path d="M2 11h32l-4 9H6z"/></svg></div>
  <h4>Kibbleton Lawsuit</h4>
  <p>Kibbleton is being sued by , Dale Morrow of<br>Discovery Bay, California. He he first<br>purchased Hearthbowl food in December or</p>
  <em>Read more</em>
</div>
<div class="abs service" style="left:478px">
  <div class="circle"><svg width="30" height="34" viewBox="0 0 30 34" fill="none" stroke="#fff" stroke-width="1.8"><path d="M9 3c-4 0-4 8 0 12v15M21 3c4 0 4 8 0 12v15"/><circle cx="9" cy="30" r="2"/><circle cx="21" cy="30" r="2"/></svg></div>
  <h4>Tidewalk 5/8" Leads On Sale</h4>
  <p>Your local Tidewalk has ALL of their 5/8"<br>Leads ON SALE for just $10!</p>
  <em>Read more</em>
</div>

<div class="abs band"></div>
<section class="abs news">
  <h3>THE LARCH CRITTER DEPOT DOG WASH<br>NEWS AND UPDATES</h3>
  <p>The Larch Critter Depot Dog Wash attendants are always here to help wash your four-legged friends, and trim their nails...but they are also here to help educate all of us! Nail trims are such an essential routine for our pups, especially if they don't run and walk as much as they would in the wild.</p>
  <p>Below are two photo that demonstrate how important nail trims are. The 'Before' shot shows the dogs two front feet. Looking at the photo the left foot ( Dogs right foot) has not been trimmed yet. Notice the two outside toes twisting out and away from the foot. The right foot ( Dogs left foot ) has already been trimmed. Notice how "cat like" the toes are, tight and together allowing the pads full access to the ground in a healthy way. Dog toe/foot pads relay information to the dog like where the ground is, what angle the slope/stairs are, etc. When toes get twisted due to long nails, signals get mixed and dogs start trying to compensate by standing differently resulting</p>
</section>
<div class="abs nail-photo"><div role="img" aria-label="Before and after photos of a dog's front paws showing untrimmed and trimmed nails"></div></div>

<aside class="abs social">
  <div class="social-head"><i></i><div><b>Pawboard</b><small>Like &nbsp; you like this.</small></div></div>
  <div class="post"><div class="thumb" role="img" aria-label="Dog photo"></div><div><h5>Finibus Bonorum et Malorum</h5><p>Lorem ipsum dolor sit amet</p><small>20 Likes &nbsp; Share</small></div></div>
  <div class="post"><div class="thumb" role="img" aria-label="Pet owner photo"></div><div><h5>Perspiciatis unde omnis unde</h5><p>Lorem ipsum dolor sit amet</p><small>20 Likes &nbsp; Share</small></div></div>
  <div class="post"><div class="thumb" role="img" aria-label="Pet owner photo"></div><div><h5>Perspiciatis unde omnis unde</h5><p>Lorem ipsum dolor sit amet</p><small>20 Likes &nbsp; Share</small></div></div>
  <p class="fans-label">You and 19 others like this page.</p>
  <div class="fans" role="img" aria-label="Grid of follower profile photos"><i></i><i></i><i></i><i></i><i></i><i></i><i></i><i></i><i></i><i></i><i></i><i></i><i></i><i></i><i></i><i></i></div>
  <p class="plugin">Social plugin</p>
</aside>

<footer class="abs footer"></footer>
<div class="abs col" style="left:60px">
  <h4>OPENING HOURS</h4>
  <p style="margin-top:10px;padding-left:12px">Monday – Saturday 9 a.m. – 6 p.m.<br>Sunday &nbsp;10 a.m. – 4 p.m<br>Dog Wash:9 a.m.-5:30 p.m.</p>
</div>
<div class="abs col" style="left:238px">
  <h4>QUICK LINKS</h4>
  <ul><li>Home</li><li>Events</li><li>Blog</li><li>About</li><li>Dog Wash</li><li>Products</li><li>Resources</li><li>Links</li><li>Contact</li></ul>
</div>
<div class="abs col" style="left:375px">
  <h4>CHIRPER UPDATES</h4>
  <div class="tweet"><i></i><div><h5>Finibus Bonorum et</h5><p>Lorem Ipsum is simply dummy<br>text of the printing<br><em>http://larchcritterdepot.com/</em><br><em>24 Minutes ago</em></p></div></div>
  <div class="tweet"><i></i><div><h5>Finibus Bonorum et</h5><p>Lorem Ipsum is simply dummy<br><em>http://larchcritterdepot.com/</em><br><em>24 Minutes ago</em></p></div></div>
</div>
<div class="abs col" style="left:548px">
  <h4>CONTACT US</h4>
  <div class="contact-row"><svg width="8" height="11" viewBox="0 0 8 11"><path fill="#fff" d="M4 0a4 4 0 0 0-4 4c0 3 4 7 4 7s4-4 4-7a4 4 0 0 0-4-4zm0 5.5A1.5 1.5 0 1 1 4 2.5a1.5 1.5 0 0 1 0 3z"/></svg><span>318 NE Cedar Hollow Ln.<br>Pinecrest, OR 97814</span></div>
  <div class="contact-row" style="font-size:9.5px"><svg width="10" height="10" viewBox="0 0 24 24"><path fill="#fff" d="M6.6 10.8a15 15 0 0 0 6.6 6.6l2.2-2.2c.3-.3.7-.4 1-.2 1.1.4 2.3.6 3.6.6.6 0 1 .4 1 1V20c0 .6-.4 1-1 1A17 17 0 0 1 3 4c0-.6.4-1 1-1h3.5c.6 0 1 .4 1 1 0 1.3.2 2.5.6 3.6.1.3 0 .7-.2 1z"/></svg><span>541-820-4417</span></div>
  <div class="contact-row"><svg width="11" height="8" viewBox="0 0 11 8"><rect width="11" height="8" fill="#fff"/><path d="M0 0l5.5 4L11 0" stroke="#b97c35" fill="none"/></svg><span>hello@larchcritterdepot.com</span></div>
</div>
<div class="abs bottom">
  <p>Copyright 2015 .LarchCritterDepot. All Rights Reserved</p>
  <div class="rounds"><i></i><i></i><i></i><i></i><i></i></div>
</div>
</body>
</html>
```